UI/ UX Design for ERP Software

We need a new UX/UI interface for a ERP software for property managers. Our CMMS / ERP solution is made based on responsive design technologies and is coded in PHP.
The overall UX to be similar to Tev Ulna - easy navigation, intuitive menus.

Industry/Entity Type

Property Management

Number of Pages Required

5+ page

Requirements
Must have
• Round dock buttons
Consistent icons across the application
Enough Spacing between buttons/icons/ menu
Consistent Font
Nice to have
• We would like the UX to allow the users to use the application without /minimum training.
Should not have
• we don't want anything that is classic with respect to UX

```html
<!DOCTYPE html>
<html lang="en">
<head>
<meta charset="utf-8">
<title>Propvia – Properties list</title>
<link href="https://fonts.googleapis.com/css2?family=Nunito+Sans:wght@400;600;700;800&display=swap" rel="stylesheet">
<style>
:root{
  --bg:#252630;
  --card:#30323f;
  --chip:#000000;
  --text:#ffffff;
  --muted:#b9bdd1;
  --blue:#0a8cff;
  --dock:#1c1d24;
  --orange:#f5743a;
  --yellow:#fbb935;
}
*{box-sizing:border-box;margin:0;padding:0}
html,body{width:1200px;height:1200px;overflow:hidden}
body{background:var(--bg);font-family:"Nunito Sans",sans-serif;color:var(--text);position:relative}
.topbar{position:absolute;left:43px;right:43px;top:46px;height:50px;display:flex;align-items:center;justify-content:space-between}
.brand{display:flex;align-items:center;gap:8px;font-size:21px;font-weight:700}
.brand-mark{width:16px;height:16px;background:var(--text);border-radius:3px}
.user{display:flex;align-items:center;gap:18px}
.theme-toggle{width:72px;height:28px;border-radius:14px;background:#1e1f27;display:flex;align-items:center;justify-content:space-around;padding:0 6px}
.welcome{font-size:14px;font-weight:600}
.welcome b{font-weight:800}
.avatar{width:46px;height:46px;border-radius:50%;background:radial-gradient(circle at 50% 40%,#b07a5e,#5a3e33 70%);box-shadow:0 4px 14px rgba(0,0,0,.5)}
.page-title{position:absolute;left:43px;top:118px;display:flex;align-items:center;gap:10px;font-size:21px;font-weight:700}
.chips{position:absolute;left:43px;top:164px;display:flex;gap:7px}
.chip{width:124px;height:38px;border-radius:5px;background:var(--chip);font-size:11px;font-weight:700;display:flex;align-items:center;justify-content:center}
.tabs{position:absolute;left:43px;top:224px;display:flex;gap:14px}
.tab{height:46px;border-radius:5px;display:flex;align-items:center;justify-content:center;gap:8px;font-size:13px;font-weight:700}
.tab-active{width:186px;background:var(--blue);box-shadow:0 6px 18px rgba(10,140,255,.3)}
.tab-outline{width:210px;border:1px solid var(--text)}
.board{position:absolute;left:43px;top:298px;display:grid;grid-template-columns:160px 770px 160px;gap:18px}
.side{display:flex;flex-direction:column;gap:21px}
.stat-card{background:var(--card);border-radius:8px;padding:20px 14px 16px;text-align:center}
.stat-title{font-size:11px;font-weight:800;line-height:1.35}
.stat-card svg.pie{margin:18px auto 18px;display:block}
.legend{list-style:none;text-align:left;padding-left:4px;font-size:11px;font-weight:700;line-height:1.55}
.legend li{display:flex;align-items:center;gap:12px}
.legend .dot{width:6px;height:6px;border-radius:50%}
.legend .pending{color:var(--muted)}
.area-card{height:177px;padding-top:18px}
.tooltip{display:inline-block;margin-top:26px;background:#fff;color:#222;font-size:9px;font-weight:700;padding:4px 12px;border-radius:3px;position:relative}
.tooltip::after{content:"";position:absolute;left:50%;bottom:-5px;margin-left:-4px;border:4px solid transparent;border-top-color:#fff;border-bottom:0}
.area{display:block;margin:0 -4px}
.sections{display:flex;flex-direction:column;gap:18px}
.section{background:var(--card);border-radius:8px;height:157px;padding:20px 16px 0}
.section h2{font-size:17px;font-weight:700;margin-bottom:14px}
.table{display:grid;grid-template-columns:109px 204px 127px 146px auto;padding-left:14px;row-gap:11px;font-size:13px}
.th{font-weight:700;font-size:14px;margin-bottom:4px}
.td{color:var(--muted)}
.dock{position:absolute;left:513px;top:1078px;width:192px;height:76px;border-radius:14px;background:var(--dock);display:flex;align-items:center;justify-content:center;gap:41px}
.dock-btn{width:50px;height:50px;border-radius:12px;display:flex;align-items:center;justify-content:center}
.dock-home{background:linear-gradient(160deg,#17b4ff,#0a6cf0)}
.dock-apps{background:linear-gradient(160deg,#ff8a3a,#f0602e)}
</style>
</head>
<body>
<header class="topbar">
  <div class="brand"><span class="brand-mark"></span>Propvia</div>
  <div class="user">
    <div class="theme-toggle">
      <svg width="18" height="18" viewBox="0 0 18 18"><circle cx="9" cy="9" r="7.5" fill="none" stroke="#4a4c5a" stroke-width="2"/></svg>
      <svg width="18" height="18" viewBox="0 0 18 18"><path d="M11 2a7 7 0 1 0 5 11A6 6 0 0 1 11 2z" fill="#fff"/></svg>
    </div>
    <p class="welcome">Welcome, <b>Dara Whitfield</b></p>
    <div class="avatar" role="img" aria-label="User profile photo"></div>
  </div>
</header>

<h1 class="page-title">
  <svg width="30" height="24" viewBox="0 0 30 24" fill="#fff"><rect x="0" y="6" width="8" height="18"/><rect x="9" y="0" width="12" height="24"/><rect x="22" y="8" width="8" height="16"/><g fill="#252630"><rect x="11" y="3" width="3" height="3"/><rect x="16" y="3" width="3" height="3"/><rect x="11" y="9" width="3" height="3"/><rect x="16" y="9" width="3" height="3"/><rect x="11" y="15" width="3" height="3"/><rect x="16" y="15" width="3" height="3"/><rect x="2" y="10" width="3" height="3"/><rect x="2" y="16" width="3" height="3"/><rect x="24" y="12" width="3" height="3"/><rect x="24" y="18" width="3" height="3"/></g></svg>
  Properties list
</h1>

<nav class="chips">
  <span class="chip">Crest tower</span><span class="chip">Crest tower</span><span class="chip">Crest tower</span><span class="chip">Crest tower</span><span class="chip">Crest tower</span><span class="chip">Crest tower</span><span class="chip">Crest tower</span>
</nav>

<div class="tabs">
  <a class="tab tab-active"><svg width="13" height="15" viewBox="0 0 13 15" fill="#fff"><rect x="0" y="2" width="13" height="13" rx="1.5"/><rect x="4" y="0" width="5" height="3" rx="1"/><g fill="#0a8cff"><rect x="3" y="6" width="7" height="1.4"/><rect x="3" y="9" width="7" height="1.4"/><rect x="3" y="12" width="5" height="1.4"/></g></svg>Request / orders</a>
  <a class="tab tab-outline"><svg width="14" height="14" viewBox="0 0 14 14" fill="#fff"><rect x="0" y="2" width="14" height="12" rx="1.5"/><rect x="3" y="0" width="2" height="4"/><rect x="9" y="0" width="2" height="4"/><rect x="3" y="8" width="3" height="3" fill="#252630"/></svg>Maintenance calendar</a>
</div>

<main class="board">
  <aside class="side">
    <div class="stat-card">
      <p class="stat-title">Tenant request by user</p>
      <svg class="pie" width="72" height="72" viewBox="0 0 80 80"><circle cx="40" cy="40" r="40" fill="#c9e3ff"/><path d="M40 40 L40 0 A40 40 0 0 1 68.3 68.3 Z" fill="#0b63e5"/></svg>
      <ul class="legend">
        <li class="pending"><span class="dot" style="background:#dce8ff"></span>No complete (100)</li>
        <li><span class="dot" style="background:#0b7bff"></span>Completed (65)</li>
      </ul>
    </div>
    <div class="stat-card">
      <p class="stat-title">Maintenance by user</p>
      <svg class="pie" width="72" height="72" viewBox="0 0 80 80"><circle cx="40" cy="40" r="40" fill="#f6d0c0"/><path d="M40 40 L40 0 A40 40 0 0 1 68.3 68.3 Z" fill="#f26f3c"/></svg>
      <ul class="legend">
        <li class="pending"><span class="dot" style="background:#dce8ff"></span>No complete (100)</li>
        <li><span class="dot" style="background:#f26f3c"></span>Completed (65)</li>
      </ul>
    </div>
  </aside>

  <section class="sections">
    <article class="section">
      <h2>Tenant request</h2>
      <div class="table">
        <span class="th">Ticket ID</span><span class="th">Subject</span><span class="th">Date</span><span class="th">Property</span><span class="th">Tenant</span>
        <span class="td">1232132323</span><span class="td">Request for rent freeze</span><span class="td">01/01/2021</span><span class="td">Crest tower</span><span class="td">Mina Carver</span>
        <span class="td">1232132323</span><span class="td">Bad neighboors</span><span class="td">01/01/2021</span><span class="td">Crest tower</span><span class="td">Mina Carver</span>
      </div>
    </article>
    <article class="section">
      <h2>Maintenance</h2>
      <div class="table">
        <span class="th">Ticket ID</span><span class="th">Subject</span><span class="th">Date</span><span class="th">Property</span><span class="th">Tenant</span>
        <span class="td">1232132323</span><span class="td">Request for rent freeze</span><span class="td">01/01/2021</span><span class="td">Crest tower</span><span class="td">Mina Carver</span>
        <span class="td">1232132323</span><span class="td">Bad neighboors</span><span class="td">01/01/2021</span><span class="td">Crest tower</span><span class="td">Mina Carver</span>
      </div>
    </article>
    <article class="section">
      <h2>Work orders</h2>
      <div class="table">
        <span class="th">Ticket ID</span><span class="th">Subject</span><span class="th">Date</span><span class="th">Property</span><span class="th">Tenant</span>
        <span class="td">1232132323</span><span class="td">Request for rent freeze</span><span class="td">01/01/2021</span><span class="td">Crest tower</span><span class="td">Mina Carver</span>
        <span class="td">1232132323</span><span class="td">Bad neighboors</span><span class="td">01/01/2021</span><span class="td">Crest tower</span><span class="td">Mina Carver</span>
      </div>
    </article>
    <article class="section">
      <h2>Purcharse orders</h2>
      <div class="table">
        <span class="th">Ticket ID</span><span class="th">Subject</span><span class="th">Date</span><span class="th">Property</span><span class="th">Tenant</span>
        <span class="td">1232132323</span><span class="td">Request for rent freeze</span><span class="td">01/01/2021</span><span class="td">Crest tower</span><span class="td">Mina Carver</span>
        <span class="td">1232132323</span><span class="td">Bad neighboors</span><span class="td">01/01/2021</span><span class="td">Crest tower</span><span class="td">Mina Carver</span>
      </div>
    </article>
  </section>

  <aside class="side">
    <div class="stat-card">
      <p class="stat-title">Montly maintenance</p>
      <svg class="pie" width="72" height="72" viewBox="0 0 80 80"><circle cx="40" cy="40" r="40" fill="#a3e6ff"/><path d="M40 40 L40 0 A40 40 0 0 1 68.3 68.3 Z" fill="#00aef5"/></svg>
      <ul class="legend">
        <li class="pending"><span class="dot" style="background:#a3e6ff"></span>No complete (100)</li>
        <li><span class="dot" style="background:#00aef5"></span>Completed (65)</li>
      </ul>
    </div>
    <div class="stat-card area-card">
      <p class="stat-title">Purcharse orders<br>this week</p>
      <span class="tooltip">8 orders</span>
      <svg class="area" width="144" height="62" viewBox="0 0 144 62"><path d="M0 62 L12 50 L20 54 L36 30 L44 40 L56 24 L66 34 L76 30 L100 0 L144 62 Z" fill="var(--yellow)"/><circle cx="66" cy="24" r="6" fill="#e89a1a" opacity=".6"/><circle cx="66" cy="24" r="3.5" fill="#f0a020"/></svg>
    </div>
  </aside>
</main>

<nav class="dock">
  <a class="dock-btn dock-home"><svg width="30" height="26" viewBox="0 0 30 26"><path d="M15 1 L29 13 L25 13 L25 25 L18 25 L18 17 L12 17 L12 25 L5 25 L5 13 L1 13 Z" fill="#fff"/><rect x="21" y="3" width="3" height="6" fill="#fff"/></svg></a>
  <a class="dock-btn dock-apps"><svg width="24" height="24" viewBox="0 0 24 24" fill="#fff"><circle cx="4" cy="4" r="2.3"/><circle cx="12" cy="4" r="2.3"/><circle cx="20" cy="4" r="2.3"/><circle cx="4" cy="12" r="2.3"/><circle cx="12" cy="12" r="2.3"/><circle cx="20" cy="12" r="2.3"/><circle cx="4" cy="20" r="2.3"/><circle cx="12" cy="20" r="2.3"/><circle cx="20" cy="20" r="2.3"/></svg></a>
</nav>
</body>
</html>
```